Email signature and business card

Australian company called Brakmere. We provide construction and maintenance services to the mining industry. I would like the design to be similar to our website theme(www.brakmere.com.au) whilst staying compact. RGB colours to include: 42,96,140 and 232,163,0 and I have attached 2 logos.

The following fields will need to be included:

Full Name
Title
Location/Project
Phone
Mobile
Fax
Email
Web site

Target Market(s)

Mining Industry

Industry/Entity Type

Construction

Requirements
Must have
• Full Name, Title, Office Address, Phone, Mobile, Fax, Email, Web address
• Back of card must include: Boilermaking, Carpentry, Concrete, Construction, Cranes, Data and Comms, Electrical, Fabrication, Fitting, Labour Hire, Plumbing, Rigging, Shutdowns

```html
<!DOCTYPE html>
<html lang="en">
<head>
<meta charset="utf-8">
<title>Brakmere – Business Card</title>
<link href="https://fonts.googleapis.com/css2?family=Open+Sans:wght@400;600;700&display=swap" rel="stylesheet">
<style>
  :root {
    --brand-blue: #2a608c;
    --brand-blue-deep: #0f5573;
    --brand-gold: #e8a300;
    --card-white: #ffffff;
    --card-grey: #f1f2f2;
    --page-bg: #e6e6e3;
    --text-light: #ffffff;
  }
  * { margin: 0; padding: 0; box-sizing: border-box; }
  html, body { width: 1200px; height: 871px; overflow: hidden; }
  body {
    background: var(--page-bg);
    font-family: "Open Sans", Arial, sans-serif;
    position: relative;
  }
  .card {
    position: absolute;
    width: 620px;
    height: 340px;
    border-radius: 4px;
    overflow: hidden;
    box-shadow: 0 6px 18px rgba(0,0,0,0.18);
  }

  /* Back of card */
  .card-back {
    left: 80px; top: 70px;
    background: linear-gradient(135deg, var(--card-white), var(--card-grey));
  }
  .brand-block {
    position: absolute;
    left: 44px; top: 96px;
    width: 180px;
    text-align: center;
  }
  .brand-mark {
    width: 82px; height: 82px;
    border-radius: 50%;
    background: var(--brand-blue-deep);
    margin: 0 auto 12px;
  }
  .brand-name {
    font-weight: 700;
    font-size: 27px;
    letter-spacing: 1px;
    color: var(--brand-blue-deep);
  }
  .brand-url {
    margin-top: 4px;
    font-weight: 700;
    font-size: 12px;
    color: var(--brand-blue-deep);
  }
  .service-list {
    position: absolute;
    top: 78px;
    list-style: none;
  }
  .service-list.col-one { left: 260px; }
  .service-list.col-two { left: 430px; }
  .service-list li {
    position: relative;
    padding-left: 26px;
    font-size: 13px;
    font-weight: 600;
    line-height: 24px;
    color: var(--brand-blue-deep);
  }
  .service-list li svg {
    position: absolute;
    left: 0; top: 7px;
    width: 13px; height: 11px;
  }

  /* Front of card */
  .card-front {
    left: 500px; top: 460px;
    background: var(--card-white);
  }
  .front-shape { position: absolute; inset: 0; }
  .front-brand {
    position: absolute;
    left: 34px; top: 84px;
    width: 190px;
    text-align: center;
  }
  .front-brand .brand-mark { width: 96px; height: 96px; }
  .front-brand .brand-name { font-size: 30px; }
  .contact {
    position: absolute;
    left: 330px; top: 70px;
    color: var(--text-light);
  }
  .contact-name { font-size: 17px; font-weight: 700; }
  .contact-title { font-size: 12px; margin-bottom: 16px; }
  .contact-company { font-size: 12px; font-weight: 700; margin-bottom: 4px; }
  .contact-address { font-size: 12.5px; margin-bottom: 10px; }
  .contact-row {
    display: flex;
    align-items: center;
    font-size: 13px;
    line-height: 23px;
  }
  .contact-row svg { width: 15px; height: 13px; margin-right: 22px; flex: none; }
</style>
</head>
<body>

<svg width="0" height="0" style="position:absolute">
  <defs>
    <symbol id="icon-tick" viewBox="0 0 13 11">
      <path d="M1 6 L5 10 L12 1" fill="none" stroke="#e8a300" stroke-width="2.4"/>
    </symbol>
  </defs>
</svg>

<section class="card card-back" aria-label="Back of business card">
  <div class="brand-block">
    <div class="brand-mark"></div>
    <div class="brand-name">BRAKMERE</div>
    <div class="brand-url">www.brakmere.com.au</div>
  </div>
  <ul class="service-list col-one">
    <li><svg><use href="#icon-tick"/></svg>Boilermaking</li>
    <li><svg><use href="#icon-tick"/></svg>Carpentry</li>
    <li><svg><use href="#icon-tick"/></svg>Concrete</li>
    <li><svg><use href="#icon-tick"/></svg>Construction</li>
    <li><svg><use href="#icon-tick"/></svg>Cranes</li>
    <li><svg><use href="#icon-tick"/></svg>Data and Comms</li>
    <li><svg><use href="#icon-tick"/></svg>Electrical</li>
  </ul>
  <ul class="service-list col-two">
    <li><svg><use href="#icon-tick"/></svg>Fabrication</li>
    <li><svg><use href="#icon-tick"/></svg>Fitting</li>
    <li><svg><use href="#icon-tick"/></svg>Labour Hire</li>
    <li><svg><use href="#icon-tick"/></svg>Plumbing</li>
    <li><svg><use href="#icon-tick"/></svg>Rigging</li>
    <li><svg><use href="#icon-tick"/></svg>Shutdowns</li>
  </ul>
</section>

<section class="card card-front" aria-label="Front of business card">
  <svg class="front-shape" viewBox="0 0 620 340" preserveAspectRatio="none">
    <defs>
      <linearGradient id="panel-fill" x1="0" y1="0" x2="1" y2="1">
        <stop offset="0" stop-color="#1a6488"/>
        <stop offset="1" stop-color="#0c4d68"/>
      </linearGradient>
    </defs>
    <path d="M260 0 C330 70 320 250 250 340 L620 340 L620 0 Z" fill="#e8a300"/>
    <path d="M272 0 C342 70 332 250 262 340 L620 340 L620 0 Z" fill="url(#panel-fill)"/>
  </svg>

  <div class="front-brand">
    <div class="brand-mark"></div>
    <div class="brand-name">BRAKMERE</div>
  </div>

  <div class="contact">
    <div class="contact-name">Mara Ellison</div>
    <div class="contact-title">CEO</div>
    <div class="contact-company">Brakmere, Inc</div>
    <div class="contact-address">Kestrelweg 18 CH - 4410 Lindenau</div>
    <div class="contact-row">
      <svg viewBox="0 0 15 13"><path d="M2 4 Q7.5 -1 13 4 L11 6 L9 4.5 L6 4.5 L4 6 Z M3 8 H12 V12 H3 Z" fill="none" stroke="#e8a300" stroke-width="1.3"/></svg>
      041 555 02 17
    </div>
    <div class="contact-row">
      <svg viewBox="0 0 15 13"><rect x="4.5" y="0.7" width="6" height="11.6" rx="1" fill="none" stroke="#e8a300" stroke-width="1.3"/></svg>
      041 555 02 17
    </div>
    <div class="contact-row">
      <svg viewBox="0 0 15 13"><rect x="1" y="5" width="13" height="6" fill="none" stroke="#e8a300" stroke-width="1.3"/><rect x="4" y="1" width="7" height="4" fill="none" stroke="#e8a300" stroke-width="1.3"/></svg>
      041 555 02 18
    </div>
    <div class="contact-row">
      <svg viewBox="0 0 15 13"><rect x="1" y="2" width="13" height="9" fill="none" stroke="#e8a300" stroke-width="1.3"/><path d="M1 2 L7.5 7 L14 2" fill="none" stroke="#e8a300" stroke-width="1.3"/></svg>
      mara@brakmere.com.au
    </div>
  </div>
</section>

</body>
</html>
```